Mental Health Therapy Website

I need a design for a mental health therapy website. It is a private practice. The business name is Fenwick Counseling, PLLC. My name is Martin Fenwick, LMHC, NCC, DCC. I would like some of the features/menus to be Home; Welcome/About Me, Rates and Services, Common Questions, and Contact.
If possible I would like a blog on the main page that I can update with articles I write. I would like the contact page to feature a map to my location (4189 Birchmont Ave. S, Lakewood, WA 98312).
I would like to place a small photo of me on the Welcome/About page.
I am new to this so if I am forgetting anything, please ask me!!
I will upload my logo so you can fit it and the color scheme into the design.
Thank you so very much!

```html
<!DOCTYPE html>
<html lang="en">
<head>
<meta charset="utf-8">
<title>Fenwick Counseling</title>
<link href="https://fonts.googleapis.com/css2?family=Open+Sans:wght@300;400;600;700&display=swap" rel="stylesheet">
<style>
:root{
  --blue:#1f4f8c;
  --nav-top:#2f5f9e;
  --nav-bottom:#244d85;
  --nav-field:#1b3f70;
  --green:#4f8a2f;
  --text:#8a8a8a;
  --title:#6a6a6a;
  --footer:#f2f2f2;
  --panel:#f4f4f4;
  --link:#4a4a4a;
}
*{margin:0;padding:0;box-sizing:border-box}
html,body{width:874px;height:1200px;overflow:hidden;background:#fff;font-family:"Open Sans",sans-serif}
.page{position:relative;width:874px;height:1200px}
.abs{position:absolute}

.brand{left:144px;top:16px;display:flex;align-items:center;gap:6px}
.brand-dot{width:34px;height:34px;border-radius:50%;background:var(--blue)}
.brand-name{font-size:19px;font-weight:600;color:var(--blue);line-height:1}

.nav{left:144px;top:73px;width:586px;height:38px;border-radius:3px;background:linear-gradient(var(--nav-top),var(--nav-bottom));display:flex;align-items:center;padding-left:19px}
.nav a{color:#fff;font-size:9px;font-weight:700;text-decoration:none;margin-right:25px}
.search{position:absolute;right:7px;top:8px;width:146px;height:20px;border-radius:3px;background:var(--nav-field);color:#9fb3cf;font-size:7.5px;padding:5px 7px}
.search svg{position:absolute;right:5px;top:4px}

.hero{left:144px;top:119px;width:586px;height:214px;background:linear-gradient(100deg,#c9d4dd,#e8e6e2 45%,#d7d2cc 75%,#b9c2c8)}
.dots{right:14px;bottom:14px;display:flex;gap:3px}
.dots span{width:10px;height:10px;border-radius:50%;background:#fff}
.dots span.on{background:var(--blue)}

h2{position:absolute;color:var(--blue);font-size:12px;font-weight:700}
.welcome-img{left:144px;top:386px;width:386px;height:124px;border-radius:3px;background:linear-gradient(180deg,#6f93c4,#c0cfe0 55%,#8aa0b8)}
.body-copy{left:144px;top:523px;width:386px;font-size:6.8px;line-height:15px;color:var(--text);font-weight:300}

.about-box{left:545px;top:377px;width:185px;height:284px;background:var(--panel)}
.about-photo{left:553px;top:385px;width:167px;height:93px;background:linear-gradient(135deg,#f4f2ee,#e2c9b2 60%,#d9553a)}
.about-copy{left:555px;top:485px;width:166px;font-size:6.8px;line-height:15px;color:var(--text);font-weight:300}

.card{position:absolute;top:717px;width:186px}
.card .img{height:88px;border-radius:3px}
.card h3{margin-top:9px;font-size:8.6px;line-height:15px;font-weight:700;color:var(--title)}
.card p{margin-top:1px;font-size:6.6px;line-height:15px;color:var(--text);font-weight:300}
.card .btn{position:absolute;top:206px;left:0;width:69px;height:21px;border-radius:3px;background:var(--blue);color:#fff;font-size:7px;display:flex;align-items:center;justify-content:center}

.footer{left:0;top:993px;width:874px;height:207px;background:var(--footer)}
.fcol{position:absolute;top:1031px}
.fcol h4{font-size:11.5px;font-weight:400;color:#555;margin-bottom:10px}
.fcol li{list-style:none;font-size:8.6px;line-height:15px;color:var(--link)}
.signup p{font-size:8.6px;color:var(--link);word-spacing:5px}
.field{width:138px;height:17px;background:#fff;border:1px solid #dcdcdc;font-size:6.5px;color:#aaa;padding:4px 8px;margin-top:14px}
.field+.field{margin-top:9px}
.subscribe{position:absolute;left:78px;top:100px;width:61px;height:15px;border-radius:8px;background:var(--blue);color:#fff;font-size:8px;font-weight:700;display:flex;align-items:center;justify-content:center}
.social li{display:flex;align-items:center;justify-content:space-between;width:90px;height:24px}
.social .ico{width:17px;height:17px;border-radius:50%;background:var(--blue)}
.copyright{left:0;top:1175px;width:874px;text-align:center;font-size:7.5px;color:#555}
</style>
</head>
<body>
<div class="page">
  <div class="abs brand"><span class="brand-dot"></span><span class="brand-name">Fenwick Counseling</span></div>

  <nav class="abs nav">
    <a>Home</a><a>About Me</a><a>Rates</a><a>Services</a><a>Common Questions</a><a>Contact</a>
    <div class="search">Search
      <svg width="12" height="12" viewBox="0 0 12 12"><circle cx="4.5" cy="4.5" r="3.3" fill="none" stroke="#fff" stroke-width="1.4"/><line x1="7" y1="7" x2="11" y2="11" stroke="#fff" stroke-width="1.8"/></svg>
    </div>
  </nav>

  <div class="abs hero" role="img" aria-label="Photo of a couple in a counseling session with a therapist">
    <div class="abs dots"><span class="on"></span><span></span><span></span><span></span></div>
  </div>

  <h2 style="left:144px;top:356px">Welcome to Fenwick Counselling</h2>
  <div class="abs welcome-img" role="img" aria-label="Photo of stacked stones by the sea"></div>
  <p class="abs body-copy">Lorem Ipsum is simply dummy text of the printing and typesetting industry. Lorem Ipsum has been the industry's standard dummy text ever since the 1500s, when an unknown printer took a galley of type and scrambled it to make a type specimen book. It has survived not only five centuries, but also the leap into electronic typesetting, remaining essentially unchanged. It was popularised in the 1960s with the release of Dryset sheets containing Lorem Ipsum passages, and more recently with desktop publishing software like Pressline Composer including versions of Lorem Ipsum.<br>Lorem Ipsum is simply dummy text of the printing and typesetting industry. Lorem Ipsum has been the industry's standard dummy text ever since the 1500s, when an unknown printer took a galley of type and scrambled it to make a type specimen book. It has survived not only five centuries</p>

  <h2 style="left:545px;top:356px">About Me</h2>
  <div class="abs about-box"></div>
  <div class="abs about-photo" role="img" aria-label="Portrait photo of the therapist"></div>
  <p class="abs about-copy">Mental health counseling/therapy for individuals (children, adolescents, adults), couples,and families. &nbsp;I am a trauma certified therapist that utilizes CBT+ to assist with trauma.<br>&nbsp;My approach to therapy is psychodynamic that utilizes tools from CBT, Solutionsfocused, Emotionsfocused, and Psychoeducation therapies to assist clients managing depression, anxiety, truama, phobias, personality disorders, ADHD, selfinjury,and communication issues. Sessions are typically 45 to 50 minutes in length.</p>

  <h2 style="left:144px;top:684px">Latest Articles</h2>
  <article class="card" style="left:144px">
    <div class="img" role="img" aria-label="Photo of two women talking on a sofa" style="background:linear-gradient(90deg,#e6dcc4,#cdb48e 50%,#e9e1cf)"></div>
    <h3>Lorem Ipsum is simply dummy text of the printing and typesetting industry.</h3>
    <p>Lorem Ipsum has been the industry's standard dummy text ever since the 1500s, when an unknown printer took a galley of type and scrambled it to make a type specimen book. It has survived not only five centuries, but also the leap into electronic typesetting ...</p>
    <span class="btn">Read More</span>
  </article>
  <article class="card" style="left:345px">
    <div class="img" role="img" aria-label="Photo of a laughing family at the beach" style="background:linear-gradient(90deg,#b8c8d2,#d9b9a2 50%,#d9706e)"></div>
    <h3>Lorem Ipsum is simply dummy text of the printing and typesetting industry.</h3>
    <p>Lorem Ipsum has been the industry's standard dummy text ever since the 1500s, when an unknown printer took a galley of type and scrambled it to make a type specimen book. It has survived not only five centuries, but also the leap into electronic typesetting ...</p>
    <span class="btn">Read More</span>
  </article>
  <article class="card" style="left:545px">
    <div class="img" role="img" aria-label="Photo of three smiling adults" style="background:linear-gradient(90deg,#e7e1da,#d8b8a0 50%,#c9a58e)"></div>
    <h3>Lorem Ipsum is simply dummy text of the printing and typesetting industry.</h3>
    <p>Lorem Ipsum has been the industry's standard dummy text ever since the 1500s, when an unknown printer took a galley of type and scrambled it to make a type specimen book. It has survived not only five centuries, but also the leap into electronic typesetting ...</p>
    <span class="btn">Read More</span>
  </article>

  <footer class="abs footer"></footer>
  <div class="fcol" style="left:143px"><h4>Quick Links</h4><ul><li>Home</li><li>About Me</li><li>Rates</li><li>Services</li><li>Common Questions</li><li>Contact</li></ul></div>
  <div class="fcol" style="left:294px"><h4>Support Links</h4><ul><li>Legal Notice</li><li>Privacy Policy</li><li>Terms &amp; Conditions</li><li>Help</li></ul></div>
  <div class="fcol signup" style="left:445px"><h4>Newsletter SignUp</h4><p>Sign-up for our daily emails by</p>
    <div class="field">Name</div><div class="field">Enter Your E-Mail ID</div><span class="subscribe">Subscribe</span></div>
  <div class="fcol social" style="left:644px"><h4>Connect With Us</h4><ul>
    <li><span class="ico"></span>Chirpline</li><li><span class="ico"></span>Friendbook</li><li><span class="ico"></span>Workmesh</li></ul></div>
  <p class="abs copyright">Copyright ©2013 Company Name &nbsp;- All rights reserved</p>
</div>
</body>
</html>
```